Business card design for sustainable building and development company

Need a business card design for a new sustainable building and real estate development company in the San Francisco Bay area. Name of company is "Tovrin Advisors, LLC" and we provide "Sustainable building, energy and development services" for residential and non residential projects. We'd like the following colors used but not all area required: green, gray, blue. Design should communicate innovation, professionalism and sustainability. Our current website is www.tovrin-advisors.example. Another possible design idea is to have the following listed on the back of the card:
Certified: VERN QS, Eco Marker Rater, DOLM Rater, Terravue Inspector, KSO TQ Building Analyst. Its not a must but could be text that could be used for back of card. Overall, we are open to a simple, clean design and or one with more text than usual for a card.

Industry/Entity Type

Real Estate

Contact Information for Business Card

Name on card: Mark J. Halvik
Title for Name: Principal + Founder
Phone: 555.814.0627
Email: mhalvik@tovrin-advisors.example
Website: www.tovrin-advisors.example

Also, please add the following for address:
San Francisco, California

Requirements
Nice to have
• If you can integrate the outline of a skyline on the backside of the card and if it looks good, I would like to see the design
Should not have
• a barcode;

```html
<!DOCTYPE html>
<html lang="en">
<head>
<meta charset="utf-8">
<title>Business Card – Consultant</title>
<link rel="stylesheet" href="https://fonts.googleapis.com/css2?family=Open+Sans:wght@400;700&display=swap">
<style>
  :root {
    --page-bg: #d9dcdf;
    --card-light: #f4f5f5;
    --card-shade: #dfe1e2;
    --brand-green: #6dbb4f;
    --crescent-black: #222222;
    --ink-white: #ffffff;
    --tower-tint: #b9dcaa;
  }
  html, body {
    margin: 0;
    padding: 0;
    width: 1200px;
    height: 865px;
    overflow: hidden;
    background: var(--page-bg);
    font-family: "Open Sans", Arial, sans-serif;
  }
  .canvas {
    position: relative;
    width: 1200px;
    height: 865px;
  }
  .business-card {
    position: absolute;
    left: 100px;
    top: 146px;
    width: 1000px;
    height: 572px;
    overflow: hidden;
    box-shadow: 0 18px 40px rgba(0,0,0,0.18);
  }
  .card-art {
    position: absolute;
    inset: 0;
    width: 1000px;
    height: 572px;
    display: block;
  }
  .contact-block {
    position: absolute;
    right: 58px;
    top: 52px;
    text-align: right;
    color: var(--ink-white);
    line-height: 1.3;
  }
  .holder-name {
    margin: 0;
    font-size: 27px;
    font-weight: 700;
  }
  .holder-title {
    margin: 0 0 58px;
    font-size: 24px;
    font-weight: 400;
  }
  .detail {
    margin: 0;
    font-size: 22px;
    font-weight: 400;
    display: flex;
    justify-content: flex-end;
    align-items: center;
    gap: 8px;
  }
  .detail.address-last { margin-bottom: 14px; }
  .detail.email-line { margin-bottom: 14px; }
  .icon {
    width: 18px;
    height: 18px;
    fill: var(--ink-white);
    flex: none;
  }
</style>
</head>
<body>
<main class="canvas">
  <section class="business-card">
    <svg class="card-art" viewBox="0 0 1000 572" xmlns="http://www.w3.org/2000/svg">
      <defs>
        <linearGradient id="cardFace" x1="0" y1="0" x2="1" y2="1">
          <stop offset="0" stop-color="var(--card-shade)"/>
          <stop offset="0.5" stop-color="var(--card-light)"/>
          <stop offset="1" stop-color="var(--card-shade)"/>
        </linearGradient>
        <radialGradient id="discFace" cx="0.62" cy="0.38" r="0.7">
          <stop offset="0" stop-color="#ffffff"/>
          <stop offset="1" stop-color="#dcdedf"/>
        </radialGradient>
        <linearGradient id="towerFade" x1="0" y1="0" x2="0" y2="1">
          <stop offset="0" stop-color="var(--tower-tint)" stop-opacity="0.75"/>
          <stop offset="1" stop-color="var(--tower-tint)" stop-opacity="0.35"/>
        </linearGradient>
      </defs>
      <rect class="card-base" width="1000" height="572" fill="url(#cardFace)"/>
      <rect class="green-field" x="330" y="0" width="670" height="512" fill="var(--brand-green)"/>
      <ellipse class="disc-border" cx="358" cy="236" rx="302" ry="334" fill="#ffffff"/>
      <ellipse class="crescent" cx="352" cy="242" rx="292" ry="324" fill="var(--crescent-black)"/>
      <ellipse class="disc" cx="318" cy="214" rx="290" ry="318" fill="url(#discFace)"/>
      <rect class="tower-illustration" x="90" y="270" width="330" height="302"
            fill="url(#towerFade)" role="img"
            aria-label="Faint green illustration of a tall office building"/>
      <rect class="base-rule" x="0" y="548" width="440" height="4" fill="var(--brand-green)" opacity="0.5"/>
    </svg>

    <div class="contact-block">
      <p class="holder-name">Lorne Abbet-Vale</p>
      <p class="holder-title">Consultant</p>
      <p class="detail">210.9th floor,Quay</p>
      <p class="detail address-last">Harbour Lane KVR</p>
      <p class="detail">555 201 4478
        <svg class="icon" viewBox="0 0 24 24" aria-hidden="true"><path d="M6.6 10.8a15.1 15.1 0 0 0 6.6 6.6l2.2-2.2a1 1 0 0 1 1-.25 11.4 11.4 0 0 0 3.6.57 1 1 0 0 1 1 1V20a1 1 0 0 1-1 1A17 17 0 0 1 3 4a1 1 0 0 1 1-1h3.5a1 1 0 0 1 1 1c0 1.25.2 2.45.57 3.57a1 1 0 0 1-.25 1z"/></svg>
      </p>
      <p class="detail">555 201 4478
        <svg class="icon" viewBox="0 0 24 24" aria-hidden="true"><path d="M7 2h8l3 3v5H7z M3 10h18v11H3z M6 13h3v2H6z M11 13h3v2h-3z M16 13h2v2h-2z M6 17h3v2H6z M11 17h3v2h-3z"/></svg>
      </p>
      <p class="detail email-line">name@mail.example
        <svg class="icon" viewBox="0 0 24 24" aria-hidden="true"><path d="M2 5h20v14H2z M3.5 6.5 12 13l8.5-6.5z" fill-rule="evenodd"/></svg>
      </p>
      <p class="detail">www.yoursitename.example</p>
    </div>
  </section>
</main>
</body>
</html>
```